Easy Marinade Labels for Butchery Store

Need a set of labels designed for a Butchery Shop. They will sit in the top left corner of the packets as a triangle (7cm each side). Easy because the only major requirement is the label name and some small text saying "Please ask in store to see spec sheet for ingredients". Extra points for finding a fun way to incorporate the logo and/or images of food (garlic bulbs, chilli, spices ect) to enhance the label. List of Marinade Names below: GarlicPepper Mint & RosemarySatayBBQChilli Plum & GingerSundried Tomato & BasilBuffaloHoney SoyHoi-SinPer PeriSpicy CajunTeriyakiBlack Bean Ive also attached the logo and an example of how the label might sit on a packet of meat. Thanks

Target Market(s)

Butchery Deli Shop Customers

Industry/Entity Type

Food Store

Font styles to use
Serif
Sans Serif
Decorative
Other font styles liked:
• Fun font that isn't a generic Quellbrix Font?

Colors

Designer to choose colors to be used in the design.

Requirements
Must have
• Product Name
• Small text saying "Please ask in store to see spec sheet for ingredients"
Nice to have
• Photos of ingredients that would match that type of marinade - Chilli, Garlic, Spices.
• Fenly Oak Logo - not essential if it doesn't look good on the label / doesn't fit.

```html
<!DOCTYPE html>
<html lang="en">
<head>
<meta charset="utf-8">
<title>Garlic Pepper Marinade Label</title>
<link rel="stylesheet" href="https://fonts.googleapis.com/css2?family=Caveat+Brush&family=Cabin:wght@700&display=swap">
<style>
  :root {
    --page-bg: #ffffff;
    --frame-yellow: #eef214;
    --spice-dark: #1c1414;
    --spice-red: #8c1f33;
    --spice-green: #6f7544;
    --garlic-cream: #d9d2c3;
    --label-text: #ffffff;
  }
  html, body {
    margin: 0;
    padding: 0;
    overflow: hidden;
    background: var(--page-bg);
  }
  .canvas {
    position: relative;
    width: 1200px;
    height: 900px;
    overflow: hidden;
    background: var(--page-bg);
  }
  .label-shape {
    position: absolute;
    inset: 0;
  }
  .marinade-name {
    position: absolute;
    left: 0;
    width: 1240px;
    top: 365px;
    margin: 0;
    text-align: center;
    font-family: "Caveat Brush", cursive;
    font-weight: 400;
    font-size: 96px;
    line-height: 92px;
    letter-spacing: 1px;
    color: var(--label-text);
  }
  .ingredients-note {
    position: absolute;
    left: 0;
    width: 1248px;
    top: 600px;
    margin: 0;
    text-align: center;
    font-family: "Cabin", sans-serif;
    font-weight: 700;
    font-size: 20.5px;
    letter-spacing: 2.2px;
    color: var(--label-text);
  }
</style>
</head>
<body>
  <main class="canvas">
    <svg class="label-shape" width="1200" height="900" viewBox="0 0 1200 900">
      <defs>
        <radialGradient id="spice-fill" cx="0.5" cy="0.55" r="0.6">
          <stop offset="0" stop-color="var(--spice-red)"/>
          <stop offset="0.45" stop-color="#4a2026"/>
          <stop offset="0.75" stop-color="var(--spice-green)" stop-opacity="0.9"/>
          <stop offset="1" stop-color="var(--spice-dark)"/>
        </radialGradient>
        <linearGradient id="garlic-glow" x1="0" y1="0" x2="1" y2="0">
          <stop offset="0" stop-color="var(--garlic-cream)" stop-opacity="0"/>
          <stop offset="0.25" stop-color="var(--garlic-cream)" stop-opacity="0.35"/>
          <stop offset="0.5" stop-color="var(--garlic-cream)" stop-opacity="0"/>
          <stop offset="0.8" stop-color="var(--garlic-cream)" stop-opacity="0.3"/>
          <stop offset="1" stop-color="var(--garlic-cream)" stop-opacity="0"/>
        </linearGradient>
      </defs>
      <g role="img" aria-label="Photo of garlic bulbs and cloves among mixed black, green and pink peppercorns">
        <polygon points="624,176 148,648 1100,648" fill="url(#spice-fill)"/>
        <polygon points="624,176 148,648 1100,648" fill="url(#garlic-glow)"/>
      </g>
      <polygon class="label-frame" points="624,174 145,650 1103,650" fill="none" stroke="var(--frame-yellow)" stroke-width="7" stroke-linejoin="miter"/>
    </svg>
    <h1 class="marinade-name">GARLIC<br>PEPPER</h1>
    <p class="ingredients-note">PLEASE ASK IN STORE TO SEE SPEC SHEET FOR INGREDIENTS</p>
  </main>
</body>
</html>
```